Tallon Electrical Business Card

We need a business card design for our family-run electrical contracting business based in Western Australia called 'Tallon Electrical'. We provide electrical services including residential, commercial and industrial. We aim for individual business cards to be made for all of our employees. We already have a company logo, which we require to be featured on the design. We would like simple, sleek and vibrant designs, which incorporate our logo and represent our business. We do not want anything involving too many graphics/images. We like the colours red, black, white and all shades of grey. The final design should communicate professionalism and trustworthiness.
We require the following contact information:
Name- Grant Pellow
EC 5871
Mobile number- 0455 870 219
Fax number (including area code)- (08) 9560 2831
Email adress- name@tallonelectrical.com.au
Electrical
- ITC Handel Bold

```html
<!DOCTYPE html>
<html lang="en">
<head>
<meta charset="utf-8">
<title>Tallon Electrical Business Card</title>
<link rel="stylesheet" href="https://fonts.googleapis.com/css2?family=Saira+Condensed:wght@700&family=Saira+Semi+Condensed:wght@400;500;700&family=Saira:wght@500;700&display=swap">
<style>
  :root {
    --backdrop: #c9cacc;
    --card: #ffffff;
    --ink: #1d1d1f;
    --ink-soft: #3a3a3c;
    --red: #d8231f;
    --rule: #2a2a2c;
  }
  * { box-sizing: border-box; margin: 0; padding: 0; }
  html, body { width: 1200px; height: 1002px; overflow: hidden; }
  body {
    background: var(--backdrop);
    display: flex;
    flex-direction: column;
    align-items: center;
    justify-content: center;
    gap: 60px;
    font-family: "Saira Semi Condensed", sans-serif;
    color: var(--ink);
  }
  .card {
    position: relative;
    width: 720px;
    height: 410px;
    background: var(--card);
    box-shadow: 0 6px 18px rgba(0,0,0,0.18);
  }

  /* Company wordmark */
  .brand {
    display: flex;
    align-items: center;
    gap: 12px;
  }
  .brand-square {
    width: 34px;
    height: 34px;
    background: var(--red);
  }
  .brand-name {
    font-family: "Saira", sans-serif;
    font-weight: 700;
    font-size: 30px;
    letter-spacing: 1px;
    text-transform: uppercase;
    color: var(--ink);
    line-height: 1;
  }

  /* Back of card */
  .card-back { display: flex; align-items: center; justify-content: center; }
  .card-back .brand-square { width: 46px; height: 46px; }
  .card-back .brand-name { font-size: 42px; }

  /* Front of card */
  .person-name {
    position: absolute;
    left: 62px;
    top: 66px;
    font-family: "Saira Condensed", sans-serif;
    font-weight: 700;
    font-size: 60px;
    line-height: 1;
    letter-spacing: 0.5px;
    text-transform: uppercase;
  }
  .person-role {
    position: absolute;
    left: 64px;
    top: 130px;
    font-family: "Saira", sans-serif;
    font-weight: 500;
    font-size: 17px;
    letter-spacing: 2px;
    text-transform: uppercase;
    color: var(--ink-soft);
  }
  .rule-horizontal {
    position: absolute;
    left: 58px;
    top: 194px;
    width: 384px;
    height: 3px;
    background: var(--rule);
  }
  .rule-vertical {
    position: absolute;
    left: 442px;
    top: 90px;
    width: 3px;
    height: 258px;
    background: var(--rule);
  }
  .contact {
    position: absolute;
    display: flex;
    align-items: center;
    gap: 8px;
    font-size: 13px;
    font-weight: 500;
    color: var(--ink-soft);
    white-space: nowrap;
  }
  .contact svg { width: 13px; height: 13px; flex: none; fill: var(--red); }
  .contact-fax { left: 64px; top: 166px; }
  .contact-mobile { left: 64px; top: 214px; }
  .contact-email { left: 232px; top: 214px; font-size: 12px; }
  .contact-web { left: 232px; top: 242px; font-size: 12px; }
  .contact-address { left: 64px; top: 270px; }

  .card-front .brand {
    position: absolute;
    left: 472px;
    top: 188px;
    gap: 9px;
  }
  .card-front .brand-square { width: 26px; height: 26px; }
  .card-front .brand-name { font-size: 22px; }
</style>
</head>
<body>

<section class="card card-back">
  <div class="brand">
    <span class="brand-square"></span>
    <span class="brand-name">Tallon Electrical</span>
  </div>
</section>

<section class="card card-front">
  <h1 class="person-name">Grant Pellow</h1>
  <p class="person-role">General Manager</p>

  <div class="contact contact-fax">
    <svg viewBox="0 0 24 24" aria-hidden="true"><path d="M6.6 10.8a15.1 15.1 0 0 0 6.6 6.6l2.2-2.2a1 1 0 0 1 1-.25 11.4 11.4 0 0 0 3.6.57 1 1 0 0 1 1 1V20a1 1 0 0 1-1 1A17 17 0 0 1 3 4a1 1 0 0 1 1-1h3.5a1 1 0 0 1 1 1c0 1.25.2 2.45.57 3.57a1 1 0 0 1-.25 1z"/></svg>
    <span>(08) 9560 2831</span>
  </div>

  <div class="rule-horizontal"></div>
  <div class="rule-vertical"></div>

  <div class="contact contact-mobile">
    <svg viewBox="0 0 24 24" aria-hidden="true"><path d="M7 1h10a2 2 0 0 1 2 2v18a2 2 0 0 1-2 2H7a2 2 0 0 1-2-2V3a2 2 0 0 1 2-2zm0 3v14h10V4zm5 15.5a1 1 0 1 0 0 2 1 1 0 0 0 0-2z"/></svg>
    <span>0455 870 219</span>
  </div>

  <div class="contact contact-email">
    <svg viewBox="0 0 24 24" aria-hidden="true"><path d="M2 5h20v14H2zm2 2v.5l8 5 8-5V7zm0 2.8V17h16V9.8l-8 5z"/></svg>
    <span>name@tallonelectrical.com.au</span>
  </div>

  <div class="contact contact-web">
    <svg viewBox="0 0 24 24" aria-hidden="true"><path d="M12 2a10 10 0 1 0 0 20 10 10 0 0 0 0-20zm6.9 6h-2.9a15 15 0 0 0-1.4-3.6A8 8 0 0 1 18.9 8zM12 4c.8 1.2 1.5 2.5 1.9 4h-3.8c.4-1.5 1.1-2.8 1.9-4zM4.3 14a8 8 0 0 1 0-4h3.3a16 16 0 0 0 0 4zm.8 2h2.9a15 15 0 0 0 1.4 3.6A8 8 0 0 1 5.1 16zM8 8H5.1a8 8 0 0 1 4.3-3.6A15 15 0 0 0 8 8zm4 12c-.8-1.2-1.5-2.5-1.9-4h3.8c-.4 1.5-1.1 2.8-1.9 4zm2.3-6H9.7a14 14 0 0 1 0-4h4.6a14 14 0 0 1 0 4zm.3 5.6A15 15 0 0 0 16 16h2.9a8 8 0 0 1-4.3 3.6zM16.4 14a16 16 0 0 0 0-4h3.3a8 8 0 0 1 0 4z"/></svg>
    <span>www.tallonelectrical.com.au</span>
  </div>

  <div class="contact contact-address">
    <svg viewBox="0 0 24 24" aria-hidden="true"><path d="M12 1a7.5 7.5 0 0 0-7.5 7.5C4.5 14.1 12 23 12 23s7.5-8.9 7.5-14.5A7.5 7.5 0 0 0 12 1zm0 10.2a2.7 2.7 0 1 1 0-5.4 2.7 2.7 0 0 1 0 5.4z"/></svg>
    <span>42 Kembla Road, Unit 3, Osborne Park WA</span>
  </div>

  <div class="brand">
    <span class="brand-square"></span>
    <span class="brand-name">Tallon Electrical</span>
  </div>
</section>

</body>
</html>
```